Creation of an elegant and modern turnkey Shopify website

Hello,

We are a new company specializing in the sale of above-ground pools. We want to create a turnkey website, ideally using Shopify. For now, we need a "showcase" site, not an e-commerce platform, with four tabs:

Home Page (an overall presentation of the company)
Our Products (an overview of all the above-ground pools we sell)
Our Projects (a page inspired by Instagram to showcase photos of our future projects)
Contact (a page with all our contact information and a contact form)

We are looking to create a highly visual, elegant, and modern website with vibrant splashes of color. We will provide the text, photos (along with instructions on where to place them on each page), and all other necessary information as attachments.

Thank you in advance for your proposals!

The Brisa Lagoon Team

Target Market(s)

Targeted at Swiss customers (a translator will need to be installed for different languages)

Industry/Entity Type

Sale of customised above-ground pools

Coding

Coded - Design and coding required

Font styles to use
Sans Serif

Colors
0094D4
00A9DD
6FCCEA
C7EBF8
E9F6FB
00AB8E
00BBA5
67D7C9
C6EFE9
E9F9F6

Requirements
Must have
• A stunning, elegant and modern look
Nice to have
• Inspiration from the colors of our logo throughout the site, but in an elegant way
Should not have
• An overly classic look for swimming pool sites

```html
<!DOCTYPE html>
<html lang="en">
<head>
<meta charset="utf-8">
<title>Brisa Lagoon – Above-Ground Pools</title>
<link rel="stylesheet" href="https://fonts.googleapis.com/css2?family=Poppins:wght@300;400;500;600;700&display=swap">
<style>
:root{
  --blue:#0094d4;
  --blue-bright:#00a9dd;
  --blue-soft:#6fccea;
  --blue-pale:#c7ebf8;
  --blue-mist:#e9f6fb;
  --ink:#2b2b2b;
  --text:#3c3c3c;
  --muted:#6b6b6b;
  --white:#ffffff;
}
*{margin:0;padding:0;box-sizing:border-box}
html,body{width:1200px;height:3476px;overflow:hidden}
body{font-family:"Poppins",sans-serif;color:var(--text);background:var(--white)}
section,header,footer{position:relative;width:1200px}
.abs{position:absolute}
.btn{position:absolute;display:flex;align-items:center;justify-content:center;height:42px;border-radius:21px;font-size:15px;font-weight:400;text-decoration:none}
.btn-solid{background:var(--blue);color:var(--white)}
.btn-light{background:var(--white);color:var(--blue)}
h2{font-weight:600;color:var(--ink);font-size:41px;line-height:1.2}
.copy{font-size:15.5px;line-height:26.7px;font-weight:300;color:var(--text)}

/* header */
.site-header{height:85px;background:var(--blue-mist)}
.brand{left:112px;top:12px;font-size:25px;line-height:30px;font-weight:300;color:var(--ink);letter-spacing:1px}
.nav{left:0;top:0;height:85px}
.nav a{position:absolute;top:31px;font-size:17px;color:var(--muted);text-decoration:none;white-space:nowrap}
.nav a.active{color:var(--blue);font-weight:600}
.search{left:1066px;top:31px}

/* hero */
.hero{height:558px;background:linear-gradient(100deg,#1f2a23 0%,#2f3e3a 35%,#4c6670 60%,#3d5b6e 80%,#28323a 100%)}
.hero-photo{inset:0}
.hero h1{position:absolute;left:111px;top:128px;width:600px;font-size:43px;line-height:54px;font-weight:600;color:var(--white)}
.hero p{position:absolute;left:111px;top:303px;width:470px;font-size:17px;line-height:30px;color:var(--white)}
.hero .btn{left:111px;top:378px;width:147px}

/* welcome */
.welcome{height:456px;text-align:center}
.welcome h2{position:absolute;left:0;right:0;top:75px}
.divider{left:549px;top:149px}
.welcome .copy{position:absolute;left:185px;top:198px;width:830px}
.welcome .btn{left:526px;top:324px;width:148px}

/* personalized */
.services{height:431px;background:var(--blue-mist)}
.services h2{position:absolute;left:108px;top:79px}
.services .copy{position:absolute;left:110px;top:149px;width:450px}
.services .btn{left:110px;top:303px;width:147px}
.services .visual{left:590px;top:150px;width:508px;height:165px;background:linear-gradient(180deg,#6fccea 0%,#c7ebf8 45%,#cfd9e0 100%)}

/* satisfaction */
.satisfaction{height:511px}
.satisfaction .visual{left:111px;top:86px;width:438px;height:339px;background:linear-gradient(135deg,#cfd9c3 0%,#8fbf9c 40%,#e78fb0 60%,#6fb9b8 100%)}
.satisfaction h2{position:absolute;left:610px;top:118px}
.satisfaction .copy{position:absolute;left:613px;top:189px;width:440px}
.satisfaction .btn{left:613px;top:330px;width:147px}

/* why */
.why{height:612px;background:radial-gradient(circle at 30% 40%,#07a0dc 0%,var(--blue) 55%,#0089c6 100%);color:var(--white);text-align:center}
.why h2{position:absolute;left:0;right:0;top:71px;color:var(--white);line-height:53px}
.feature{position:absolute;top:225px;width:240px;margin-left:-120px}
.feature .badge{width:104px;height:104px;border-radius:50%;background:var(--white);margin:0 auto;display:flex;align-items:center;justify-content:center}
.feature h3{margin-top:18px;font-size:22px;font-weight:600;line-height:30px}
.feature p{margin:8px auto 0;width:205px;font-size:12.5px;line-height:18px;font-weight:300}
.why .btn{left:526px;top:483px;width:148px}

/* contact */
.contact{height:513px}
.contact h2{position:absolute;left:108px;top:117px}
.contact .copy{position:absolute;left:110px;top:188px;width:445px}
.contact .tagline{position:absolute;left:110px;top:329px;font-size:19px;font-weight:600;color:var(--ink)}
.contact .btn{left:110px;top:376px;width:148px}
.contact .visual{left:652px;top:87px;width:437px;height:339px;background:radial-gradient(circle at 45% 55%,#7fdde4 0%,#3cbfd1 45%,#1b7fa6 100%)}

/* footer */
.site-footer{height:310px;background:var(--blue-mist)}
.site-footer h4{position:absolute;top:42px;font-size:20px;font-weight:400;color:var(--ink)}
.site-footer ul{position:absolute;top:86px;list-style:none}
.site-footer li{font-size:14px;line-height:24px;color:var(--muted);font-weight:300}
.footer-about{left:112px;top:86px;width:280px;font-size:14px;line-height:22px;color:var(--muted);font-weight:300}
.footer-details{left:112px;top:147px}
.footer-details div{display:flex;align-items:center;gap:5px;font-size:14px;line-height:27px;color:var(--muted);font-weight:300}
.gallery{left:791px;top:48px;width:298px;height:185px;display:grid;grid-template-columns:repeat(3,1fr);grid-template-rows:repeat(2,1fr)}
.gallery div:nth-child(1){background:linear-gradient(135deg,#3aa9d8,#e38ab0)}
.gallery div:nth-child(2){background:linear-gradient(135deg,#2b3a34,#46a8c8)}
.gallery div:nth-child(3){background:linear-gradient(135deg,#5fbfe3,#2d6fa8)}
.gallery div:nth-child(4){background:linear-gradient(135deg,#6d8a5a,#4a7fb5)}
.gallery div:nth-child(5){background:linear-gradient(135deg,#3f6a3d,#5cb9dc)}
.gallery div:nth-child(6){background:linear-gradient(135deg,#2f9fd6,#f0c440)}
.copyright{left:112px;top:267px;font-size:14px;color:var(--ink);font-weight:300}
</style>
</head>
<body>

<header class="site-header">
  <div class="abs brand">BRISA<br>LAGOON</div>
  <nav class="abs nav">
    <a class="active" style="left:510px" href="#">Home</a>
    <a style="left:607px" href="#">Our Products</a>
    <a style="left:764px" href="#">Our Work</a>
    <a style="left:888px" href="#">Contact Us</a>
  </nav>
  <svg class="abs search" width="24" height="24" viewBox="0 0 24 24" fill="none" stroke="#555" stroke-width="1.8"><circle cx="10.5" cy="10.5" r="7.5"/><line x1="16" y1="16" x2="22" y2="22"/></svg>
</header>

<section class="hero">
  <div class="abs hero-photo" role="img" aria-label="Above-ground pool with a metal ladder in a garden at dusk"></div>
  <h1>Transform Your Garden With Our Premium Above-Ground Pools!</h1>
  <p>Achieve your dreams with our custom, tailor-made above-ground pools</p>
  <a class="btn btn-light" href="#">Get Started</a>
</section>

<section class="welcome">
  <h2>Welcome To Brisa Lagoon</h2>
  <svg class="abs divider" width="102" height="12" viewBox="0 0 102 12"><line x1="0" y1="1" x2="68" y2="1" stroke="var(--blue)" stroke-width="1.5"/><line x1="34" y1="11" x2="102" y2="11" stroke="var(--blue)" stroke-width="1.5"/></svg>
  <p class="copy">Imagine an exceptional relaxation and leisure space right in your own backyard. With our unparalleled expertise and commitment to excellence, we create above-ground pools that exceed all expectations. Our exclusive, custom-designed models are crafted to combine style, durability, and innovation, offering a unique and refined experience</p>
  <a class="btn btn-solid" href="#">Read More</a>
</section>

<section class="services">
  <h2>Personalized Services</h2>
  <p class="copy">We understand that every garden and client is unique. That's why we offer personalized services, from design to installation and after-sales support. Our team of experts is here to answer all your questions and guide you throughout your project</p>
  <a class="btn btn-solid" href="#">Read More</a>
  <div class="abs visual" role="img" aria-label="Photo of a round white above-ground pool filled with blue water"></div>
</section>

<section class="satisfaction">
  <div class="abs visual" role="img" aria-label="Mother and daughter relaxing on a pink float in an above-ground pool"></div>
  <h2>Guaranteed Satisfaction</h2>
  <p class="copy">Your satisfaction is our top priority. We are committed to providing you with exceptional service and the highest quality products. Join our community of satisfied customers who are already enjoying their custom above-ground pools. 10-Year Warranty!</p>
  <a class="btn btn-solid" href="#">Read More</a>
</section>

<section class="why">
  <h2 style="color:#fff">Why Choose<br>Our Above-Ground Pools?</h2>
  <div class="feature" style="left:215px">
    <div class="badge"><svg width="56" height="60" viewBox="0 0 56 60" fill="none" stroke="var(--blue)" stroke-width="3.5"><circle cx="28" cy="24" r="18"/><circle cx="28" cy="24" r="11"/><path d="M16 38 L10 56 L18 52 L22 58 L26 42"/><path d="M40 38 L46 56 L38 52 L34 58 L30 42"/><path d="M28 17 l2 5 h5 l-4 3 2 5 -5 -3 -5 3 2 -5 -4 -3 h5z" fill="var(--blue)" stroke="none"/></svg></div>
    <h3>Superior Quality</h3>
    <p>Each pool is constructed with high-quality materials, ensuring exceptional durability and strength.</p>
  </div>
  <div class="feature" style="left:467px">
    <div class="badge"><svg width="66" height="56" viewBox="0 0 66 56" fill="none" stroke="var(--blue)" stroke-width="3.5" stroke-linecap="round"><path d="M44 40 V8 a5 5 0 0 1 10 0"/><path d="M54 40 V8 a5 5 0 0 1 10 0"/><line x1="44" y1="18" x2="54" y2="18"/><line x1="44" y1="28" x2="54" y2="28"/><rect x="4" y="22" width="58" height="30" rx="15"/><path d="M12 36 q5 -4 10 0 t10 0 t10 0"/><path d="M12 44 q5 -4 10 0 t10 0 t10 0 t10 0"/></svg></div>
    <h3>Elegant Design</h3>
    <p>Our pools come in a variety of styles and finishes, seamlessly blending into any garden setting.</p>
  </div>
  <div class="feature" style="left:720px">
    <div class="badge"><svg width="58" height="58" viewBox="0 0 58 58"><path d="M24 3h10l2 7 6 3 7-3 6 9-5 5v7l5 5-6 9-7-3-6 3-2 7H24l-2-7-6-3-7 3-6-9 5-5v-7l-5-5 6-9 7 3 6-3z" fill="var(--blue)"/><circle cx="29" cy="29" r="13" fill="#fff"/><circle cx="29" cy="29" r="10" fill="none" stroke="var(--blue)" stroke-width="3"/><path d="M23 29 l4 4 8-8" fill="none" stroke="var(--blue)" stroke-width="3.5" stroke-linecap="round"/></svg></div>
    <h3>Easy Installation</h3>
    <p>Enjoy your new oasis quickly with our simple and fast installation process.</p>
  </div>
  <div class="feature" style="left:979px">
    <div class="badge"><svg width="60" height="60" viewBox="0 0 60 60" fill="none" stroke="var(--blue)" stroke-width="3.5" stroke-linecap="round"><path d="M20 30 a12 12 0 1 1 20 0 c-3 4 -4 7 -4 10 h-12 c0 -3 -1 -6 -4 -10z"/><line x1="24" y1="46" x2="36" y2="46"/><line x1="26" y1="52" x2="34" y2="52"/><path d="M25 24 l5 6 5 -6"/><line x1="30" y1="4" x2="30" y2="9"/><line x1="10" y1="12" x2="14" y2="16"/><line x1="50" y1="12" x2="46" y2="16"/><line x1="4" y1="28" x2="9" y2="28"/><line x1="56" y1="28" x2="51" y2="28"/></svg></div>
    <h3>Constant Innovation</h3>
    <p>We incorporate the latest technologies to provide you with an optimal and safe swimming experience.</p>
  </div>
  <a class="btn btn-light" href="#">View More</a>
</section>

<section class="contact">
  <h2>Contact Us Today</h2>
  <p class="copy">Don't wait any longer to transform your garden into a wellness oasis. Contact us today to discover our range of customizable above-ground pools and get a tailored quote. Dive into a world of infinite possibilities with Brisa Lagoon</p>
  <p class="tagline">We Bring Your Pool Dreams to Life!</p>
  <a class="btn btn-solid" href="#">Contact Us</a>
  <div class="abs visual" role="img" aria-label="Above-ground pool with a donut float, beach ball and ladder"></div>
</section>

<footer class="site-footer">
  <h4 style="left:112px">Contact Us</h4>
  <p class="abs footer-about">Imagine an exceptional relaxation and leisure space right in your own</p>
  <div class="abs footer-details">
    <div><svg width="11" height="14" viewBox="0 0 12 16"><path d="M6 0a6 6 0 0 1 6 6c0 4-6 10-6 10S0 10 0 6a6 6 0 0 1 6-6z" fill="var(--blue)"/><circle cx="6" cy="6" r="2.2" fill="#fff"/></svg>Chemin des Vignes 27 1820 Montreux</div>
    <div><svg width="12" height="12" viewBox="0 0 16 16"><path d="M3 1l3 3-2 3c1 2 3 4 5 5l3-2 3 3-2 3C7 15 1 9 1 3z" fill="var(--blue)"/></svg>079 000 12 34</div>
    <div><svg width="13" height="10" viewBox="0 0 16 12"><rect width="16" height="12" rx="1.5" fill="var(--blue)"/><path d="M1 1l7 6 7-6" fill="none" stroke="#fff" stroke-width="1.4"/></svg>hello@brisalagoon.ch</div>
  </div>
  <h4 style="left:439px">Quick Links</h4>
  <ul style="left:439px"><li>Home</li><li>About Us</li><li>Our Products</li><li>Our Works</li><li>Contact Us</li></ul>
  <h4 style="left:605px">Other Links</h4>
  <ul style="left:605px"><li>FAQs</li><li>Terms Of Services</li><li>Privacy Policy</li><li>Sitemaps</li><li>Help Center</li></ul>
  <div class="abs gallery" role="img" aria-label="Grid of six photos of customer pools and swimmers">
    <div></div><div></div><div></div><div></div><div></div><div></div>
  </div>
  <p class="abs copyright">Copyright © 2024 Brisa Lagoon. All Rights Reserved.</p>
</footer>

</body>
</html>
```